Scented Candle Company Sticker Design for Packaging

We need a Sticker design for our various scented candle packages. Our handmade candles incorperate hand crafted Chiyogami Paper imported from Japan, which is wrapped around the jar. Each of the scents have different papers assigned to them and although we would like a general design in which the text can be changed according to each scent we would also like if the beautiful Japanese paper designs could be subtly incorporated in the design.

We want the the text of the sticker and logo of our company to be printed in gold foil once printed and our featured logo image is of a Dogwood tree. We think that perhaps the inclusion of dogwood blossom/s might look nice in the design but is not a must have!

We are fond of the delicate and classic print designs and etching designs. We would also like the design to be in a portrait rectangle that is closer in the shape of a square/ or not too long of a rectangle, and, would like to have a boarder on the edge of the sticker (this could incorporate the blossom if you wish, I have attached an image for reference/ inspiration) but we are after something much more simplistic and draws less attention to the eye and connected in the boarder.

Our brand is elegant and classic and we would like to be in keeping with our style. We have attached some images of the candles and our logo for inspiration, we do not want the stickers for the candle themselves but rather to place on the packaging.

Ive left some information for one of the candle scents for this design but once again I would like to reiterate that the design should allow for interchangeable titles for the other fragrances.

Coastal Fig Meadow(in smaller writing).
Coastal Fig Meadow, Orange blossom, cinnamon.

Our candles are hand made in Australia and a made from 100% soy wax and we would like to to be presented on the label.

I would like to mention again that we are looking for an elegant and classic design. We are looking for a simplistic design/layout that also focuses on the fine details. It should be striking but also not overbearing with an air of sophistication with minimal to no use of colours in encouraged.

I have also attached a font that is matched to the "candle co." underneath the tree in the logo.
Updates

I only just posted the design request, but first created the brief on the 2nd. I would like more time for the designers to both see my review and have an adequate amount of time to work on the project.

Target Market(s)

Up Market Shoppers.

Font styles to use
Script
Other font styles liked:
• Acorn

Colors
fbfbfb

Requirements
Must have
• Logo on the sticker.
Nice to have
• Nice to have a dogwood blossom incorporated into the boarder but must be simplistic as it doesn't want to be the main focus of the sticker
Should not have
• Photographs in the sticker design. Must be graphic design. No to little colour.

```html
<!DOCTYPE html>
<html lang="en">
<head>
<meta charset="utf-8">
<title>Hollowbrook Candle Co. — Coastal Fig Meadow Label</title>
<link rel="stylesheet" href="https://fonts.googleapis.com/css2?family=Marcellus&family=Josefin+Sans:wght@400&display=swap">
<style>
  :root {
    --backdrop: #000000;
    --label: #ffffff;
    --ink: #111111;
    --ornament-tone: #e4e4e4;
  }
  html, body {
    margin: 0;
    padding: 0;
    width: 1200px;
    height: 1200px;
    overflow: hidden;
    background: var(--backdrop);
  }
  .sticker { display: block; width: 1200px; height: 1200px; }
  .label-sheet { fill: var(--label); }
  .frame { fill: none; stroke: var(--ink); stroke-width: 2.8; }
  .corner-ornament { fill: var(--ornament-tone); }
  .brand-mark { fill: var(--ink); }
  .rule { stroke: var(--ink); stroke-width: 1.8; }
  .brand-name {
    font-family: "Marcellus", serif;
    font-size: 60px;
    letter-spacing: 8px;
    fill: var(--ink);
  }
  .brand-sub {
    font-family: "Josefin Sans", sans-serif;
    font-size: 25px;
    letter-spacing: 3px;
    fill: var(--ink);
  }
  .scent-name {
    font-family: "Josefin Sans", sans-serif;
    font-size: 23px;
    letter-spacing: 0.5px;
    fill: var(--ink);
  }
  .details {
    font-family: "Josefin Sans", sans-serif;
    font-size: 17px;
    letter-spacing: 0.5px;
    fill: var(--ink);
  }
</style>
</head>
<body>
<svg class="sticker" viewBox="0 0 1200 1200" xmlns="http://www.w3.org/2000/svg">
  <rect class="label-sheet" x="217" y="217" width="766" height="766"/>

  <rect class="frame" x="245" y="258" width="713" height="691"/>

  <rect class="corner-ornament" role="img" aria-label="Line-drawn blossom cluster, top left corner" x="242" y="249" width="114" height="116" rx="18"/>
  <rect class="corner-ornament" role="img" aria-label="Line-drawn blossom cluster, top right corner" x="847" y="249" width="113" height="118" rx="18"/>
  <rect class="corner-ornament" role="img" aria-label="Line-drawn blossom cluster, bottom left corner" x="242" y="842" width="114" height="113" rx="18"/>
  <rect class="corner-ornament" role="img" aria-label="Line-drawn blossom cluster, bottom right corner" x="847" y="842" width="113" height="113" rx="18"/>

  <circle class="brand-mark" role="img" aria-label="Hollowbrook Candle Co. brand mark" cx="602" cy="440" r="80"/>

  <text class="brand-name" x="604" y="600" text-anchor="middle">HOLLOWBROOK</text>
  <text class="brand-sub" x="600" y="646" text-anchor="middle">CANDLE CO.</text>

  <line class="rule" x1="358" y1="772" x2="834" y2="772"/>
  <line class="rule" x1="403" y1="703" x2="403" y2="808"/>
  <line class="rule" x1="789" y1="703" x2="789" y2="808"/>

  <text class="scent-name" x="596" y="757" text-anchor="middle">COASTAL FIG MEADOW</text>
  <text class="details" x="596" y="814" text-anchor="middle">100% SOY WAX</text>
  <text class="details" x="596" y="846" text-anchor="middle">MADE IN AUSTRALIA</text>
</svg>
</body>
</html>
```